Harborline Renewal Business Card Design

Professional and clean design. The design colors should flow with the logo. Two-sided card with the website on the back which is:

www.HarborlineRenewal.example.

"Specializing in Water Damage Restoration"

On the front I need the name, email, phone, and logo.

Name: Darnell Quisby
Email: Darnell@HarborlineRenewal.example
Phone: 555-318-2046 for now

I only have the Preview and Thumbnail right now but should have the source files uploaded within a day or two.

Target Market(s)

Flood victims, home owners with water damage from busted pipes etc...

Industry/Entity Type

Business

Contact Information for Business Card

Name: Darnell Quisby

Font styles to use
Serif
Sans Serif

Requirements
Must have
• Business Card Details Info

```html
<!DOCTYPE html>
<html lang="en">
<head>
<meta charset="utf-8">
<title>Harborline Renewal Business Card</title>
<link rel="stylesheet" href="https://fonts.googleapis.com/css2?family=Cinzel:wght@400;600&family=Open+Sans:wght@400&display=swap">
<style>
  :root {
    --page: #ececec;
    --card-black: #050505;
    --card-white: #ffffff;
    --brand-blue: #2f97d6;
    --brand-light: #5bbfee;
    --ink-grey: #555555;
    --rule-grey: #c8c8c8;
    --band-text: #ffffff;
  }
  * { box-sizing: border-box; margin: 0; padding: 0; }
  html, body { width: 1200px; height: 1120px; overflow: hidden; }
  body {
    background: var(--page);
    position: relative;
    font-family: "Open Sans", Arial, sans-serif;
  }
  .card {
    position: absolute;
    left: 150px;
    width: 900px;
    height: 514px;
    box-shadow: 0 6px 18px rgba(0,0,0,0.18);
    overflow: hidden;
  }

  /* Back side */
  .card-back {
    top: 40px;
    background: var(--card-black);
    display: flex;
    flex-direction: column;
    align-items: center;
  }
  .back-mark {
    margin-top: 58px;
    width: 210px;
    height: 210px;
    border-radius: 50%;
    background: var(--brand-blue);
  }
  .back-name {
    margin-top: 30px;
    font-family: "Cinzel", Georgia, serif;
    font-weight: 600;
    font-size: 34px;
    letter-spacing: 2px;
    color: var(--brand-blue);
  }
  .back-tagline {
    margin-top: 40px;
    font-family: "Cinzel", Georgia, serif;
    font-weight: 400;
    font-size: 27px;
    letter-spacing: 1px;
    color: var(--brand-blue);
  }

  /* Front side */
  .card-front {
    top: 586px;
    background: var(--card-white);
  }
  .brand-block {
    position: absolute;
    left: 50px;
    top: 110px;
    width: 340px;
    display: flex;
    flex-direction: column;
    align-items: center;
  }
  .brand-mark {
    width: 110px;
    height: 110px;
    border-radius: 50%;
    background: var(--brand-blue);
  }
  .brand-name {
    margin-top: 18px;
    font-family: "Cinzel", Georgia, serif;
    font-weight: 600;
    font-size: 38px;
    line-height: 1.1;
    text-align: center;
    color: var(--brand-blue);
  }
  .divider {
    position: absolute;
    left: 425px;
    top: 110px;
    width: 2px;
    height: 190px;
    background: var(--rule-grey);
  }
  .contact-block {
    position: absolute;
    left: 460px;
    top: 105px;
  }
  .person-name {
    font-family: "Cinzel", Georgia, serif;
    font-weight: 600;
    font-size: 30px;
    color: var(--brand-blue);
    letter-spacing: 0.5px;
  }
  .person-title {
    font-family: "Cinzel", Georgia, serif;
    font-weight: 400;
    font-size: 22px;
    color: var(--ink-grey);
    letter-spacing: 1px;
    margin-top: 2px;
  }
  .contact-list {
    list-style: none;
    margin-top: 24px;
  }
  .contact-list li {
    display: flex;
    align-items: center;
    gap: 12px;
    font-size: 19px;
    color: #333;
    line-height: 34px;
  }
  .contact-list svg { width: 18px; height: 18px; flex: none; }
  .band-rule {
    position: absolute;
    left: 0; right: 0;
    bottom: 82px;
    height: 3px;
    background: var(--brand-blue);
  }
  .tagline-band {
    position: absolute;
    left: 0; right: 0;
    bottom: 0;
    height: 74px;
    background: var(--brand-blue);
    display: flex;
    align-items: center;
    justify-content: center;
    font-family: "Cinzel", Georgia, serif;
    font-size: 27px;
    letter-spacing: 1px;
    color: var(--band-text);
  }
</style>
</head>
<body>

<section class="card card-back" aria-label="Card back">
  <div class="back-mark"></div>
  <div class="back-name">Harborline Renewal</div>
  <p class="back-tagline">Specializing in Water Damage Restoration</p>
</section>

<section class="card card-front" aria-label="Card front">
  <div class="brand-block">
    <div class="brand-mark"></div>
    <div class="brand-name">Harborline<br>Renewal</div>
  </div>

  <div class="divider"></div>

  <div class="contact-block">
    <h1 class="person-name">Darnell Quisby</h1>
    <p class="person-title">Title</p>
    <ul class="contact-list">
      <li>
        <svg viewBox="0 0 20 20" aria-hidden="true">
          <circle cx="10" cy="10" r="9" fill="none" stroke="#2f97d6" stroke-width="2"/>
          <path d="M7 5.5c-1 1-1 3 .8 5.5s3.8 3.6 5 3l.9-1.2-2-1.6-1 .8c-.8-.3-2.2-1.8-2.5-2.6l.8-1-1.5-2.1z" fill="#2f97d6"/>
        </svg>
        555-318-2046
      </li>
      <li>
        <svg viewBox="0 0 20 20" aria-hidden="true">
          <rect x="2" y="5" width="16" height="11" rx="1.5" fill="#2f97d6"/>
          <path d="M2.5 5.8 10 11l7.5-5.2" fill="none" stroke="#fff" stroke-width="1.5"/>
        </svg>
        Darnell@HarborlineRenewal.example
      </li>
      <li>
        <svg viewBox="0 0 20 20" aria-hidden="true">
          <circle cx="10" cy="10" r="8" fill="none" stroke="#2f97d6" stroke-width="1.8"/>
          <ellipse cx="10" cy="10" rx="3.5" ry="8" fill="none" stroke="#2f97d6" stroke-width="1.5"/>
          <path d="M2 10h16M3.5 6h13M3.5 14h13" stroke="#2f97d6" stroke-width="1.3"/>
        </svg>
        www.HarborlineRenewal.example
      </li>
    </ul>
  </div>

  <div class="band-rule"></div>
  <p class="tagline-band">Specializing in Water Damage Restoration</p>
</section>

</body>
</html>
```